Cupcakes blog redesign - cartoon/illustrated style

I need to redesign my food blog muffinmeadow.net.

I really like the current blog design but I want to change Pagecraft theme to responsive and I want to refresh the look of the blog.

Blog design must be in the same style (cartoon, illustrated). The whole idea should be the same as old blog! The header illustration is some kind of garden full of cupcakes. All other elements (left sidebar menu, right sidebar widgets and footer elements) should be in that (garden of cupcakes) style.

The color sheme should be similar to old design. I really like pink, green and light blue color! The content background color must be white.
Only element that must be the same with old site is cupcakes thumbnail images (image 1 in attachment).
Feel fre to change all other elements design .

You can use illustration from http://artstallbin.net/search?utf8=%E2%9C%93&term=cupcakes. I will buy these elements later!

You can find all technical details (dimensions,elements...) in the attachment.

This is the list of sites I really like:

1. I adore header of this site - http://www.runbyquick.net/
2. I adore header of this site - http://pel.vorastudio.net/
3. Big site title and overal design - http://tulbarforyouth.net/
4. Header - http://pel.vorastudio.net/
5. Footer style :) - http://www.mirelotash.net/
6. Color sheme - http://brisklypan.net/
7. Color sheme - http://www.plumvoralee.net/
8. Color sheme - http://www.nolasugarbite.net/

Feel free to contact me for more information.

Good luck

Here is couple illustration example I really like. Of course it should be in Muffin Meadow style:

1. http://42sketchhub.net/web-design/contests/create-best-site-kids-world-267986/entries/29767275
2. http://42sketchhub.net/web-design/contests/create-best-site-kids-world-267986/entries/89
3. http://layoutbrix.net/demo/wp/tot-lawn/
4. http://www.bramblecritters.net/login/forums

```html
<!DOCTYPE html>
<html lang="en">
<head>
<meta charset="utf-8">
<title>Muffin Meadow – Cupcakes Recipes &amp; Ideas</title>
<link href="https://fonts.googleapis.com/css2?family=Open+Sans:wght@400;600;700&display=swap" rel="stylesheet">
<style>
:root{
  --page-bg:#f5f1e3;
  --white:#ffffff;
  --sky-top:#7cc3ea;
  --sky-low:#dff1f8;
  --grass:#9fce4c;
  --grass-dark:#76b02d;
  --nav-top:#fdf7e6;
  --nav-bottom:#f7e4b8;
  --pink:#e2335a;
  --pink-soft:#f9dbe3;
  --title-red:#8e3a2c;
  --text:#4a4a4a;
  --text-soft:#6d6d6d;
  --green-link:#4aa329;
  --ribbon-top:#fce6a6;
  --ribbon-bottom:#f6c96a;
  --cream:#f8f1de;
  --cream-border:#f2ddb0;
  --search-red:#a4442f;
  --link-red:#d3363b;
  --rule:#e6e0d0;
  --col-rule:#f4e3b8;
}
*{box-sizing:border-box;margin:0;padding:0}
html,body{width:1200px;height:2206px;overflow:hidden}
body{background:var(--page-bg);font-family:"Open Sans",Arial,sans-serif;color:var(--text);position:relative}
a{color:inherit;text-decoration:none}

/* header */
.header-scene{position:absolute;left:0;top:0;width:1200px;height:380px;
  background:linear-gradient(180deg,var(--sky-top) 0%,var(--sky-low) 55%,var(--grass) 80%,var(--grass-dark) 100%)}
.brand{position:absolute;left:370px;top:0;width:420px;height:106px;background:rgba(255,255,255,.92);
  text-align:center;box-shadow:0 2px 6px rgba(0,0,0,.08)}
.brand-name{font-size:44px;font-weight:700;color:var(--pink);line-height:64px;padding-top:4px}
.brand-tagline{font-size:16px;font-weight:600;color:#444;margin-top:-4px}

.main-nav{position:absolute;left:0;top:352px;width:1200px;height:70px;
  background:linear-gradient(180deg,var(--nav-top),var(--nav-bottom))}
.main-nav a{position:absolute;top:20px;font-size:18px;color:#333;line-height:30px}
.main-nav a.current{background:var(--white);color:var(--pink);padding:0 14px;border-radius:3px 3px 0 0}

/* container */
.content-sheet{position:absolute;left:34px;top:423px;width:1142px;height:1640px;background:var(--white)}

/* left sidebar */
.cat-ribbon{position:absolute;left:41px;width:268px;height:38px;
  background:linear-gradient(180deg,var(--ribbon-top),var(--ribbon-bottom));
  clip-path:polygon(0 0,100% 0,94% 50%,100% 100%,0 100%);
  font-size:17px;font-weight:600;color:var(--title-red);line-height:38px;padding-left:50px}
.cat-dot{position:absolute;left:40px;width:40px;height:40px;border-radius:50%;background:var(--pink);border:3px solid #fff;box-shadow:0 0 0 1px #f1c0cc}
.cat-dot::after{content:"";position:absolute;left:11px;top:11px;width:12px;height:12px;border-radius:50%;background:#fff}
.flavour-list{position:absolute;left:41px;top:488px;width:268px;list-style:none}
.flavour-list li{height:39px;line-height:39px;font-size:16px;border-bottom:1px solid var(--rule);padding-left:51px;position:relative;color:#333}
.flavour-list li::before{content:"›";position:absolute;left:18px;font-size:18px;color:#555}
.flavour-list li.active{color:var(--green-link)}
.flavour-list li.active::before{color:var(--green-link)}
.ad-badge{position:absolute;left:110px;top:1053px;width:128px;height:128px;
  background:linear-gradient(180deg,#f7c9d6,#c8e39a);border:1px solid #d9d9d9}
.ad-tower{position:absolute;left:115px;top:1209px;width:122px;height:613px;
  background:linear-gradient(180deg,#1d4f86 0%,#9fb6cc 25%,#8a8f7f 55%,#5d7f3c 70%,#153b66 78%,#153b66 100%)}

/* center column */
.post-column{position:absolute;left:335px;top:423px;width:488px;height:1617px;
  border-left:2px solid var(--col-rule);border-right:2px solid var(--col-rule)}
.post{position:absolute;left:0;width:486px;height:400px}
.post-title{position:absolute;left:16px;top:12px;width:450px;font-size:21px;font-weight:600;line-height:26px;color:var(--title-red)}
.post-date{position:absolute;left:16px;top:70px;font-size:13px;color:#333}
.post-thumb{position:absolute;left:20px;top:109px;width:202px;height:203px;background:var(--pink-soft);border:2px dotted #f1b8c6;padding:14px}
.post-thumb span{display:block;width:100%;height:100%}
.post-excerpt{position:absolute;left:245px;top:120px;width:232px;font-size:13.3px;line-height:22.5px;color:#555}
.read-more{display:block;color:var(--link-red);margin-top:0}
.post-cats{position:absolute;left:14px;top:328px;width:459px;height:37px;background:var(--cream);font-size:13px;line-height:37px;padding-left:14px;color:#444}
.pager{position:absolute;left:198px;top:1588px;display:flex;gap:3px}
.pager span{width:22px;height:23px;background:#ddd;border-radius:3px;font-size:10px;color:#fff;text-align:center;line-height:23px}
.pager span.on{background:#888}
.pager i{font-style:normal;width:22px;text-align:center;color:#aaa;line-height:23px}

/* right sidebar */
.follow{position:absolute;left:851px;top:440px;font-size:12px;color:#333;display:flex;align-items:center;gap:6px}
.follow b{display:block;width:32px;height:32px;border-radius:50%;background:var(--pink)}
.follow b:nth-child(even){background:var(--grass-dark)}
.search-box{position:absolute;left:848px;top:485px;width:321px;height:99px;background:var(--search-red);border-radius:4px}
.search-box h3{font-size:21px;font-weight:400;color:#fff;padding:10px 0 0 14px}
.search-field{position:absolute;left:14px;top:46px;width:292px;height:36px;background:#fff;border-radius:2px;font-size:13px;color:#999;line-height:36px;padding-left:14px}
.search-field svg{position:absolute;right:8px;top:9px}
.widget{position:absolute;left:848px;width:321px;background:var(--cream);border:4px solid var(--cream-border);border-top-width:0}
.widget h3{font-size:21px;font-weight:400;color:var(--title-red);padding:8px 0 6px 10px}
.widget-inner{background:#fff;margin:0 2px 4px}
.sponsors{top:592px;height:192px}
.sponsor-ad{position:absolute;top:46px;width:153px;height:140px}
.popular{top:795px;height:264px}
.popular ul{list-style:none;padding:14px 14px 10px 24px}
.popular li{font-size:13.3px;line-height:20px;color:#333;position:relative;padding-left:16px;margin-bottom:9px}
.popular li::before{content:"›";position:absolute;left:0;top:-1px;color:var(--pink);font-size:17px;font-weight:700}
.about{position:absolute;left:851px;top:1080px;width:316px}
.about h2{font-size:25px;font-weight:600;color:var(--link-red);margin-bottom:6px}
.about p{font-size:13.3px;line-height:21px;color:#555;margin-bottom:10px}
.fan-box{position:absolute;left:879px;top:1420px;width:258px;height:249px;border:1px solid #ddd;border-top:2px solid #999;font-size:11px;color:#333}
.fan-avatar{position:absolute;left:12px;top:8px;width:50px;height:50px;background:linear-gradient(135deg,#c9c1b4,#8b8276)}
.fan-name{position:absolute;left:70px;top:10px;font-size:13px;color:#3b5998}
.fan-like{position:absolute;left:70px;top:32px;height:20px;padding:0 8px 0 22px;background:#4e69a2;color:#fff;font-size:11px;line-height:20px;border-radius:2px}
.fan-like::before{content:"";position:absolute;left:6px;top:5px;width:10px;height:10px;background:#fff}
.fan-count{position:absolute;left:12px;top:76px;font-size:11px}
.fan-count a{color:#3b5998}
.fan-faces{position:absolute;left:12px;top:100px;display:grid;grid-template-columns:repeat(4,52px);gap:4px}
.fan-faces span{height:50px;background:linear-gradient(135deg,#d6d6d6,#8d8d8d)}
.fan-faces span:nth-child(3n){background:linear-gradient(135deg,#6b6042,#2c2a22)}
.fan-foot{position:absolute;left:0;bottom:0;width:100%;height:22px;border-top:1px solid #e5e5e5;font-size:10px;color:#777;line-height:22px;padding-left:14px}

/* footer */
.footer-scene{position:absolute;left:0;top:2063px;width:1200px;height:143px;
  background:linear-gradient(180deg,var(--page-bg) 0%,var(--page-bg) 62%,var(--grass) 78%,var(--grass-dark) 100%)}
.footer-links{position:absolute;left:0;top:2085px;width:1200px;text-align:center;font-size:13.5px;color:#333}
.footer-copy{position:absolute;left:0;top:2116px;width:1200px;text-align:center;font-size:13.5px;color:#333}
</style>
</head>
<body>

<div class="header-scene" role="img" aria-label="Illustrated cupcake garden: blue sky with sun and balloon, big pink cupcake, small cupcakes, children and a village on green hills"></div>
<div class="brand">
  <div class="brand-name">Muffin Meadow</div>
  <div class="brand-tagline">Cupcakes Recipes &amp; Ideas Showcase Site</div>
</div>

<nav class="main-nav">
  <a class="current" style="left:120px">Home</a>
  <a style="left:250px">About us</a>
  <a style="left:389px">Recipes</a>
  <a style="left:517px">Category</a>
  <a style="left:656px">Video</a>
  <a style="left:769px">Testimonials</a>
  <a style="left:938px">Contact us</a>
</nav>

<div class="content-sheet"></div>

<!-- left sidebar -->
<aside>
  <div class="cat-ribbon" style="top:438px">Cupcake by Flavour</div>
  <div class="cat-dot" style="top:436px"></div>
  <ul class="flavour-list">
    <li class="active">Vanilla &amp; White cupcakes</li>
    <li>Chocolate cupttcakes</li>
    <li>Red velvet cupcakes</li>
    <li>Carrot cupcakes</li>
    <li>Caramel &amp; Coffee cupcakes</li>
    <li>Beer &amp; Liquor cupcakes</li>
    <li>Peanut butter cupcakes</li>
    <li>Other cupcake flavors</li>
  </ul>
  <div class="cat-ribbon" style="top:817px">Fruit Cupcakes</div>
  <div class="cat-dot" style="top:815px"></div>
  <div class="cat-ribbon" style="top:868px">Holiday Cupcakes</div>
  <div class="cat-dot" style="top:866px"></div>
  <div class="cat-ribbon" style="top:920px">Events Cupcakes</div>
  <div class="cat-dot" style="top:918px"></div>
  <div class="cat-ribbon" style="top:971px">Special Cupcakes</div>
  <div class="cat-dot" style="top:969px"></div>
  <div class="ad-badge" role="img" aria-label="Square blog badge with a cartoon cupcake"></div>
  <div class="ad-tower" role="img" aria-label="Tall home builder advert with a house photo"></div>
</aside>

<!-- posts -->
<main class="post-column">
  <article class="post" style="top:0">
    <h2 class="post-title">Grasshopper Cupcakes by The Busy Bakers of Elmwood</h2>
    <div class="post-date">Posted on | March 5, 2014</div>
    <div class="post-thumb"><span role="img" aria-label="Photo of a chocolate-dipped mint cupcake" style="background:linear-gradient(180deg,#b49b86,#5a3422 55%,#3a2216)"></span></div>
    <p class="post-excerpt">Chocolate mint combo is so tasty, especially when it comes in cupcake form like these Grasshopper Cupcakes by The Busy Bakers of Elmwood. These rich chocolate cupcakes are topped with a large mound of mint buttercream frosting<a class="read-more">READ MORE »</a></p>
    <div class="post-cats">Category : Chocolate cupcakes, Cupcake recipes</div>
  </article>
  <article class="post" style="top:400px">
    <h2 class="post-title">Grasshopper Cupcakes by The Busy Bakers of Elmwood</h2>
    <div class="post-date">Posted on | March 5, 2014</div>
    <div class="post-thumb"><span role="img" aria-label="Photo of a cupcake with pink frosting and a blackberry" style="background:linear-gradient(180deg,#6e6a6e,#d7a6c8 40%,#caa37a 75%,#2b2520)"></span></div>
    <p class="post-excerpt">Chocolate mint combo is so tasty, especially when it comes in cupcake form like these Grasshopper Cupcakes by The Busy Bakers of Elmwood. These rich chocolate cupcakes are topped with a large mound of mint buttercream frosting<a class="read-more">READ MORE »</a></p>
    <div class="post-cats">Category : Chocolate cupcakes, Cupcake recipes</div>
  </article>
  <article class="post" style="top:799px">
    <h2 class="post-title">Grasshopper Cupcakes by The Busy Bakers of Elmwood</h2>
    <div class="post-date">Posted on | March 5, 2014</div>
    <div class="post-thumb"><span role="img" aria-label="Photo of a caramel nut cupcake" style="background:linear-gradient(180deg,#5d3b22,#c98a4a 45%,#8a5424)"></span></div>
    <p class="post-excerpt">Chocolate mint combo is so tasty, especially when it comes in cupcake form like these Grasshopper Cupcakes by The Busy Bakers of Elmwood. These rich chocolate cupcakes are topped with a large mound of mint buttercream frosting<a class="read-more">READ MORE »</a></p>
    <div class="post-cats">Category : Chocolate cupcakes, Cupcake recipes</div>
  </article>
  <article class="post" style="top:1199px">
    <h2 class="post-title">Grasshopper Cupcakes by The Busy Bakers of Elmwood</h2>
    <div class="post-date">Posted on | March 5, 2014</div>
    <div class="post-thumb"><span role="img" aria-label="Photo of a chocolate chip cupcake with cream frosting" style="background:linear-gradient(180deg,#3a2a22,#eadac0 35%,#c9ad84 60%,#6a4a2e)"></span></div>
    <p class="post-excerpt">Chocolate mint combo is so tasty, especially when it comes in cupcake form like these Grasshopper Cupcakes by The Busy Bakers of Elmwood. These rich chocolate cupcakes are topped with a large mound of mint buttercream frosting<a class="read-more">READ MORE »</a></p>
    <div class="post-cats">Category : Chocolate cupcakes, Cupcake recipes</div>
  </article>
  <div class="pager">
    <span class="on">1</span><span>2</span><span>3</span><span>4</span><span>5</span><span>6</span><span>7</span><span>8</span><span>›</span><i>…</i><span>»</span>
  </div>
</main>

<!-- right sidebar -->
<aside>
  <div class="follow">Follow us on : <b></b><b></b><b></b><b></b><b></b><b></b></div>
  <div class="search-box">
    <h3>Search entire blog</h3>
    <div class="search-field">Keyword
      <svg width="18" height="18" viewBox="0 0 18 18"><circle cx="7" cy="7" r="5" fill="none" stroke="#888" stroke-width="2"/><line x1="11" y1="11" x2="16" y2="16" stroke="#888" stroke-width="2.4"/></svg>
    </div>
  </div>
  <section class="widget sponsors">
    <h3>Our Sponsors</h3>
    <div class="sponsor-ad" style="left:6px;background:linear-gradient(180deg,#fff 0%,#7fd3dc 60%,#b07a4d 100%)" role="img" aria-label="Advert for healthy cupcake recipes with a teal frosted cupcake"></div>
    <div class="sponsor-ad" style="left:161px;background:linear-gradient(180deg,#ffffff 45%,#9fd1e6 80%,#5ea94a 100%)" role="img" aria-label="Advert for selling diabetic test strips"></div>
  </section>
  <section class="widget popular">
    <h3>Most Popular Cupcakes</h3>
    <div class="widget-inner">
      <ul>
        <li>Cookie Dough Cupcakes with Spice Cookie Frosting</li>
        <li>Gourmet Nutty Cup Peanut Butter Cup Cupcakes</li>
        <li>Caramel Apple Starry Bar Cupcakes</li>
        <li>Marla's Brownie Cupcakes</li>
        <li>Blackberry Cupcakes</li>
      </ul>
    </div>
  </section>
  <section class="about">
    <h2>About Muffin Meadow</h2>
    <p>Nullam a purus justo. Nulla a fermentum risus, sed tristique odio. Curabitur eu lacinia magna, vel dictum nibh. Aliquam varius tincidunt volutpat. Phasellus euismod arcu non neque egestas, id semper quam suscipit. Morbi ac purus vitae urna volutpat interdum eu eu mauris.</p>
    <p>Fusce condimentum euismod accumsan. Morbi blandit rhoncus vehicula. Nunc ultrices id libero venenatis varius. Quisque viverra leo ac enim consectetur, ut consequat libero rutrum. Vivamus consectetur accumsan nibh vehicula vulputate. Maecenas at quam sed ante faucibus varius.</p>
  </section>
  <div class="fan-box">
    <div class="fan-avatar" role="img" aria-label="Page profile photo"></div>
    <div class="fan-name">Muffin Meadow</div>
    <div class="fan-like">Свиђа ми се</div>
    <div class="fan-count">5,410 people like <a>Muffin Meadow</a>.</div>
    <div class="fan-faces" role="img" aria-label="Grid of follower profile photos">
      <span></span><span></span><span></span><span></span><span></span><span></span><span></span><span></span>
    </div>
    <div class="fan-foot">Social plugin</div>
  </div>
</aside>

<footer>
  <div class="footer-scene" role="img" aria-label="Green grass strip with bushes and trees"></div>
  <div class="footer-links">Home | Contribute | Advertise | Contact</div>
  <div class="footer-copy">Copyright © 2014 Muffin Meadow. All rights reserved.</div>
</footer>

</body>
</html>
```